Project Overview:
We are looking to create a website for a monthly subscription IPTV service in WordPress. The website should provide a seamless user experience for customers to sign up for the service and manage their account information. We need the following pages: Home Page, Product Page, Sign-Up Page, and Account Information Page.

Home Page:
The Home Page design should be simple and clean, with a dark theme and minimalistic design elements. We would like to include graphics of popular movie shows displayed on multiple devices. The page should highlight the key benefits and features of our service and provide a clear call-to-action for visitors to sign up.

Product Page:
The Product Page should provide detailed information about our subscription tiers and pricing plans. It should highlight the key features of each plan and provide a clear comparison between them. The page should also include a call-to-action button for visitors to sign up.

Sign-Up Page:
The Sign-Up Page is the conversion page where members will sign up for the service. It should collect the following information: Name, Phone Number, Email, Password, and Payment Information. The design should be simple, intuitive, and easy to use. It should highlight the benefits of our service and provide a clear call-to-action for visitors to sign up.

Account Information Page:
The Account Information Page should allow members to view and manage their account details. It should include the following information: Profile Image, Contact Details, Password Management, Payment Information Management, and Membership Expiration Date. The design should be user-friendly, intuitive, and easy to navigate.

Goals: The primary goal of the website is to provide an easy-to-use portal for customers to sign up for the service and manage their account information. The website should be user-friendly and visually appealing to attract potential customers.

Scope: The scope of the project includes designing a home page, a sign-up page, an account information page, and a payment information page. The website should be designed to be responsive and accessible on desktop and mobile devices.

Design Preferences: The design should be clean, modern, and visually appealing. The use of a color palette that is consistent with the brand identity is recommended. The website should be easy to navigate and provide a clear call-to-action for users to sign up for the service.

FYI: The subscription service I am designing a website for is related to an IPTV service. IPTV stands for Internet Protocol Television, which is a digital television broadcasting protocol that uses the internet to deliver TV programs and videos to viewers. The website will allow customers to sign up for the IPTV service and access their account information such as user name and password, membership tier, name, and payment details. Please let me know if you have any further questions, and I would be happy to provide more details. Thank you!

Dear Designers,

Thank you for your participation in our project. After reviewing the designs received so far, we have decided to update the brief to better reflect our needs and preferences. We apologize for any confusion this may cause, but we believe that these changes will result in better design submissions and a more successful project overall.

The updated brief is as follows:

We are looking to create a website for WordPress.

Also, here is the updated Brief.

Project Title: WordPress Website Design for Monthly Subscription IPTV Service

Project Overview:
We are looking to create a website for a monthly subscription IPTV service. The website should provide a seamless user experience for customers to sign up for the service and manage their account information. We need the following pages: Home Page, Product Page, Sign-Up Page, and Account Information Page.

Home Page:

Product Page:

Sign-Up Page:

Account Information Page:

Design Preferences:
We prefer a dark theme with minimalistic design elements and hits of our logo colors. The website should be easy to use and navigate, with clear calls-to-action and simple, intuitive forms. The design should be optimized for mobile devices and load quickly.

We hope that these updates provide you with a clearer understanding of our requirements and preferences. Please let us know if you have any questions or concerns. We look forward to seeing your revised designs.

Thank you again for your participation.
We will guarantee this project as soon as we see something we like that meets the updated requirements.

The website's target audience is individuals who are interested in subscribing to the monthly service.

4 page

• One item for sale and a client profile section.

```html
<!DOCTYPE html>
<html lang="en">
<head>
<meta charset="utf-8">
<title>VIEWNOVA – IPTV Subscription</title>
<link href="https://fonts.googleapis.com/css2?family=Roboto:wght@400;500;700;900&family=Rubik:ital,wght@1,800;1,900&display=swap" rel="stylesheet">
<style>
:root{
  --red:#e50914;
  --red-bright:#ff1a1a;
  --black:#000;
  --panel:#0d0d0d;
  --card:#141414;
  --grey:#1b1b1b;
  --text:#ffffff;
  --muted:#c9c9c9;
}
*{box-sizing:border-box;margin:0;padding:0}
html,body{width:1200px;height:4083px;overflow:hidden;background:var(--black);color:var(--text);font-family:'Roboto',sans-serif}
.page{position:relative;width:1200px;height:4083px}
.abs{position:absolute}
.btn{position:absolute;display:flex;align-items:center;justify-content:center;gap:10px;background:var(--red);color:#fff;font:700 15px 'Roboto',sans-serif;text-transform:uppercase;border-radius:3px}
.btn svg{width:14px;height:14px}
.btn-outline{position:absolute;display:flex;align-items:center;justify-content:center;border:1px solid var(--red);color:#fff;font:700 15px 'Roboto',sans-serif;border-radius:3px}
.heading{font-family:'Rubik',sans-serif;font-style:italic;font-weight:900;color:var(--red);text-transform:uppercase;letter-spacing:-0.5px;text-shadow:0 0 0 #fff,1px 1px 0 #fff,-1px -1px 0 #fff,1px -1px 0 #fff,-1px 1px 0 #fff}
.brand{display:flex;align-items:center;gap:10px;font:900 40px 'Roboto',sans-serif;color:#fff;letter-spacing:1px}
.brand-mark{width:22px;height:22px;background:var(--red)}

/* nav */
.nav{top:0;left:0;width:1200px;height:80px;background:#000}
.nav .brand{position:absolute;left:113px;top:18px}
.nav-links{position:absolute;left:604px;top:30px;display:flex;gap:38px;font:500 16px 'Roboto',sans-serif}
.nav-links .active{color:var(--red)}
.nav .btn{left:957px;top:18px;width:132px;height:44px;font-size:16px}

/* hero */
.hero{top:80px;left:0;width:1200px;height:612px;background:linear-gradient(100deg,#2a2a2a 0%,#3b3530 30%,#274552 62%,#0a6c8a 100%)}
.hero-shade{top:80px;left:0;width:760px;height:612px;background:linear-gradient(90deg,rgba(0,0,0,.55),rgba(0,0,0,0))}
.hero-welcome{left:108px;top:240px;font:italic 900 28px 'Rubik',sans-serif}
.hero-title{left:106px;top:280px;font:italic 900 100px/1 'Rubik',sans-serif;letter-spacing:-1px}
.hero-text{left:109px;top:402px;width:470px;font-size:16px;line-height:26px}

/* about */
.about-img{left:102px;top:778px;width:478px;height:454px;border-radius:24px;background:linear-gradient(135deg,#cfc4b6,#8c8176 55%,#6b7887);border-bottom:4px solid var(--red);border-left:4px solid var(--red)}
.about-title{left:637px;top:800px;font-size:36px}
.about-text{left:637px;top:862px;width:470px;font-size:15.5px;line-height:26px;text-align:justify;color:#e8e8e8}

/* features */
.features{top:1318px;left:0;width:1200px;height:614px;background:repeating-linear-gradient(120deg,#161616 0 120px,#1c1c1c 120px 240px)}
.features-title{left:0;width:1200px;top:1396px;text-align:center;font-size:36px}
.feature{position:absolute;top:1518px;width:314px;height:324px;background:#0a0a0a;border-radius:48px 0 48px 0;text-align:center;padding-top:32px}
.feature-icon{width:94px;height:94px;border-radius:50%;background:#262626;margin:0 auto;display:flex;align-items:center;justify-content:center}
.feature-icon.on{background:var(--red)}
.feature h3{font:700 18px 'Roboto',sans-serif;margin-top:20px}
.feature p{font-size:14.5px;line-height:22px;color:#d6d6d6;margin:14px 20px 0}
.feature .more{display:flex;justify-content:center;align-items:center;gap:8px;font:700 14.5px 'Roboto',sans-serif;margin-top:16px}

/* movies */
.movies-title{left:0;width:1200px;top:2010px;text-align:center;font-size:36px}
.movie{position:absolute;width:310px;height:468px;background:#0f0f0f;border-radius:14px;text-align:center;padding:8px}
.movie-img{height:226px;border-radius:4px}
.movie h3{font:500 15px 'Roboto',sans-serif;margin-top:40px;text-transform:uppercase}
.movie p{font-size:14.5px;line-height:24px;color:#cfcfcf;margin:12px 14px 0}
.movie .btn-outline{left:87px;bottom:36px;width:136px;height:42px}

/* benefits */
.benefit-bg{top:2680px;left:0;width:1200px;height:533px;background:linear-gradient(135deg,#141414,#1f1f1f 50%,#0c0c0c)}
.benefit-img{top:2680px;left:0;width:594px;height:533px;background:linear-gradient(120deg,#2e2823,#5b4634 45%,#8a6a45 70%,#3e3a36)}
.benefit-title{left:680px;top:2724px;font-size:34px}
.benefit-list{left:680px;top:2790px;list-style:none}
.benefit-list li{display:flex;align-items:center;gap:14px;font-size:15.5px;height:43px}
.benefit-list svg{width:15px;height:15px}

/* signup */
.signup{top:3213px;left:0;width:1200px;height:447px;background:radial-gradient(ellipse at center,#1e1e1e,#0b0b0b 70%)}
.signup-title{left:0;width:1200px;top:3290px;text-align:center;font:italic 800 34px 'Rubik',sans-serif;color:var(--red)}
.signup-text{left:160px;width:880px;top:3362px;text-align:center;font-size:16px;line-height:26px}

/* footer */
.footer{top:3660px;left:0;width:1200px;height:423px;background:radial-gradient(ellipse at 40% 70%,#1a1a1a,#050505 70%)}
.footer .brand{position:absolute;left:112px;top:3726px}
.social{left:148px;top:3812px;display:flex;gap:16px}
.social span{width:16px;height:16px;border-radius:50%;background:#fff}
.f-head{font:700 17px 'Roboto',sans-serif}
.contact-item{display:flex;gap:10px;margin-top:14px;font-size:13px;line-height:17px}
.contact-item b{display:block;font-weight:700;font-size:12px}
.contact-item svg{width:12px;height:12px;flex:none;margin-top:2px}
.f-links{list-style:none;font-size:13.5px}
.f-links li{margin-top:16px}
.divider{left:113px;top:3978px;width:976px;height:1px;background:#3a3a3a}
.goup{left:1010px;top:3969px;width:80px;height:18px;border-radius:9px;background:#4a4a4a;font:700 11px 'Roboto',sans-serif;display:flex;align-items:center;justify-content:center;gap:4px}
.bottom{top:4018px;font-size:13px}
</style>
</head>
<body>
<div class="page">

<svg width="0" height="0" style="position:absolute">
  <defs>
    <symbol id="arrow-circle" viewBox="0 0 16 16"><circle cx="8" cy="8" r="7.5" fill="currentColor"/><path d="M5 8h6M8.5 5.2 11.2 8 8.5 10.8" stroke="#e50914" stroke-width="1.8" fill="none"/></symbol>
    <symbol id="arrow-circle-dark" viewBox="0 0 16 16"><circle cx="8" cy="8" r="7.5" fill="#fff"/><path d="M5 8h6M8.5 5.2 11.2 8 8.5 10.8" stroke="#000" stroke-width="1.8" fill="none"/></symbol>
    <symbol id="bullet" viewBox="0 0 16 16"><circle cx="8" cy="8" r="6.5" fill="none" stroke="#e50914" stroke-width="2"/><path d="M5.5 8h5M8.5 6 10.5 8 8.5 10" stroke="#e50914" stroke-width="1.6" fill="none"/></symbol>
  </defs>
</svg>

<!-- navigation -->
<header class="abs nav">
  <div class="brand"><span class="brand-mark"></span>VIEWNOVA</div>
  <nav class="nav-links"><span class="active">HOME</span><span>|</span><span>PRODUCT</span><span>|</span><span>SIGN UP</span></nav>
  <a class="btn">LOGIN <svg viewBox="0 0 14 14"><circle cx="7" cy="4" r="3" fill="#fff"/><path d="M1.5 13.5c0-3.5 2.5-5.5 5.5-5.5s5.5 2 5.5 5.5z" fill="#fff"/></svg></a>
</header>

<!-- hero -->
<section>
  <div class="abs hero" role="img" aria-label="Friends relaxing on a sofa watching television in a living room"></div>
  <div class="abs hero-shade"></div>
  <div class="abs hero-welcome">WELCOME TO</div>
  <div class="abs hero-title">VIEWNOVA</div>
  <p class="abs hero-text">Lorem ipsum dolor sit amet consectetur adipiscing elit sed do eiusmod tempor incididunt ut labore et dolore magna aliqua.</p>
  <a class="btn" style="left:109px;top:478px;width:160px;height:46px">GET STARTED <svg><use href="#arrow-circle"/></svg></a>
</section>

<!-- about -->
<section>
  <div class="abs about-img" role="img" aria-label="Couple on a sofa using a remote to browse a smart TV menu"></div>
  <h2 class="abs heading about-title">ABOUT VIEWNOVA</h2>
  <p class="abs about-text">Lorem ipsum dolor sit amet consectetur adipiscing elited sed do eiusmod tempor incididunt ut labore et dolore magna aliqua. Ut enim ad minim veniam, quis nostrud exercitation ullamco laboris nisi ut aliquip ex ea commodo consequat. Duis aute irure dolor in reprehenderit in voluptate velit esse cillum dolore eu fugiat nulla pariatur. Exceptteur sint occaecat cupidatat non proident, sunt in culpa qui officia deserunt mollit anim id est laboruLorem ipsum dolor sit amet, consectetur adipiscing elit, sed do eiusmod tempor incididunt ut labore et dolore magna aliqua. Ut enim ad minim veniam, nostrud exercitation ullamco laboris nisi aliquipcommodo consequat. Duis aute irure reprehenderit in voluptate velit esseg.</p>
  <a class="btn" style="left:637px;top:1175px;width:158px;height:46px">LEARN MOTRE <svg><use href="#arrow-circle"/></svg></a>
</section>

<!-- features -->
<section>
  <div class="abs features"></div>
  <h2 class="abs heading features-title">FEATURES OF OUR SERVICE</h2>
  <div class="feature" style="left:113px">
    <div class="feature-icon"><svg width="52" height="52" viewBox="0 0 52 52" fill="none" stroke="#e50914" stroke-width="2"><rect x="6" y="10" width="40" height="26" rx="2"/><path d="M20 44h12M26 36v8"/><circle cx="26" cy="23" r="6"/></svg></div>
    <h3>Lorem ipsum dolor sit amet</h3>
    <p>Lorem ipsum dolor sit amet consectetur adipiscing eiusmoded tempor incididunt labore et dolore magna aliqua enim ad minim veniam nostrud exercitation.</p>
    <div class="more">READ MORE <svg width="14" height="14"><use href="#arrow-circle-dark"/></svg></div>
  </div>
  <div class="feature" style="left:445px">
    <div class="feature-icon on"><svg width="52" height="52" viewBox="0 0 52 52" fill="none" stroke="#fff" stroke-width="2"><rect x="6" y="8" width="40" height="24" rx="2"/><rect x="20" y="22" width="12" height="24" rx="3"/><circle cx="26" cy="28" r="2"/><path d="M23 34h6M23 38h6M23 42h6"/></svg></div>
    <h3>Lorem ipsum dolor sit amet,</h3>
    <p>Lorem ipsum dolor sit amet consectetur adipiscing eiusmoded tempor incididunt labore et dolore magna aliqua enim ad minim veniam nostrud exercitation.</p>
    <div class="more">READ MORE <svg width="14" height="14"><use href="#arrow-circle-dark"/></svg></div>
  </div>
  <div class="feature" style="left:775px">
    <div class="feature-icon"><svg width="52" height="52" viewBox="0 0 52 52" fill="none" stroke="#e50914" stroke-width="2"><rect x="6" y="10" width="40" height="28" rx="2"/><path d="M18 44h16M26 38v6"/><circle cx="26" cy="24" r="7"/><path d="M26 17v14M19 24h14"/></svg></div>
    <h3>Lorem ipsum dolor sit amet,</h3>
    <p>Lorem ipsum dolor sit amet consectetur adipiscing eiusmoded tempor incididunt labore et dolore magna aliqua enim ad minim veniam nostrud exercitation.</p>
    <div class="more">READ MORE <svg width="14" height="14"><use href="#arrow-circle-dark"/></svg></div>
  </div>
</section>

<!-- popular shows -->
<section>
  <h2 class="abs heading movies-title">POPULAR MOVIE SHOWS</h2>
  <article class="movie" style="left:108px;top:2100px">
    <div class="movie-img" role="img" aria-label="Audience seated in a red cinema hall" style="background:linear-gradient(180deg,#2a0805,#8c1d10 60%,#c2391c)"></div>
    <h3>Lorem ipsum dolor sit amet</h3>
    <p>Lorem ipsum dolor sit ametconsectetur adipiscing elited sed do eiusmod tempor incididunt ut labore eted dolore magna.</p>
    <a class="btn-outline">READ MORE</a>
  </article>
  <article class="movie" style="left:445px;top:2124px">
    <div class="movie-img" role="img" aria-label="Video editing desk with monitors and control panel" style="background:linear-gradient(160deg,#3a3a3a,#1c1c1c 55%,#7a1414)"></div>
    <h3>Lorem ipsum dolor sit amet</h3>
    <p>Lorem ipsum dolor sit ametconsectetur adipiscing elited sed do eiusmod tempor incididunt ut labore eted dolore magna.</p>
    <a class="btn-outline">READ MORE</a>
  </article>
  <article class="movie" style="left:782px;top:2100px">
    <div class="movie-img" role="img" aria-label="Viewer with popcorn watching a streaming menu on TV" style="background:linear-gradient(150deg,#6a5a52,#b89a84 45%,#3b2f2b)"></div>
    <h3>Lorem ipsum dolor sit amet</h3>
    <p>Lorem ipsum dolor sit ametconsectetur adipiscing elited sed do eiusmod tempor incididunt ut labore eted dolore magna.</p>
    <a class="btn-outline">READ MORE</a>
  </article>
</section>

<!-- key benefit -->
<section>
  <div class="abs benefit-bg"></div>
  <div class="abs benefit-img" role="img" aria-label="Person watching a wall of shows on TV in a warmly lit room"></div>
  <h2 class="abs heading benefit-title">KEY BENEFIT</h2>
  <ul class="abs benefit-list">
    <li><svg><use href="#bullet"/></svg>Lorem ipsum dolor sit amet consectetur adipiscing elit</li>
    <li><svg><use href="#bullet"/></svg>Lorem ipsum dolor sit amet consectetur adipiscing elit</li>
    <li><svg><use href="#bullet"/></svg>Lorem ipsum dolor sit amet consectetur adipiscing elit</li>
    <li><svg><use href="#bullet"/></svg>Lorem ipsum dolor sit amet consectetur adipiscing elit</li>
    <li><svg><use href="#bullet"/></svg>Lorem ipsum dolor sit amet consectetur adipiscing elit</li>
    <li><svg><use href="#bullet"/></svg>Lorem ipsum dolor sit amet consectetur adipiscing elit</li>
    <li><svg><use href="#bullet"/></svg>Lorem ipsum dolor sit amet consectetur adipiscing elit</li>
  </ul>
  <a class="btn" style="left:680px;top:3115px;width:158px;height:46px">LEARN MOTRE <svg><use href="#arrow-circle"/></svg></a>
</section>

<!-- sign up -->
<section>
  <div class="abs signup"></div>
  <h2 class="abs signup-title">SIGN UP</h2>
  <p class="abs signup-text">Lorem ipsum dolor sit amet, consectetur adipiscing elit, sed do eiusmod tempor incididunt ut labore et dolore magna aliqua. Ut enim ad minim veniam, quis nostrud exercitation ullamco laboris nisi ut aliquip ex ea commodo consequat. Duis aute irure dolor in reprehenderit in voluptate velit esse cillum dolore eu fugiat nulla pariatur. Excepteur sint occaecat cupidatat non proident, sunt in culpa qui officia deserunt mollit anim id est laborum</p>
  <a class="btn" style="left:522px;top:3500px;width:156px;height:46px">LEARN MOTE <svg><use href="#arrow-circle"/></svg></a>
</section>

<!-- footer -->
<footer>
  <div class="abs footer"></div>
  <div class="brand"><span class="brand-mark"></span>VIEWNOVA</div>
  <div class="abs social"><span></span><span></span><span></span><span></span></div>

  <div class="abs" style="left:383px;top:3724px">
    <div class="f-head">Contact Us</div>
    <div class="contact-item"><svg viewBox="0 0 12 12"><path d="M2 1l2.5 0 1 3-1.5 1a6 6 0 0 0 3 3l1-1.5 3 1V10a1 1 0 0 1-1 1A9 9 0 0 1 1 2a1 1 0 0 1 1-1z" fill="#e50914"/></svg><div><b>Phone</b>+1 888 888 8888</div></div>
    <div class="contact-item"><svg viewBox="0 0 12 12"><rect x="0.5" y="2" width="11" height="8" fill="#e50914"/><path d="M.5 2 6 6.5 11.5 2" stroke="#000" fill="none"/></svg><div><b>Email</b>info@viewnova.com</div></div>
    <div class="contact-item"><svg viewBox="0 0 12 12"><path d="M6 11.5S2 7 2 4.5a4 4 0 0 1 8 0C10 7 6 11.5 6 11.5z" fill="#e50914"/><circle cx="6" cy="4.5" r="1.4" fill="#000"/></svg><div><b>Location</b>939 Lorem ipsum dolor sit amet<br>consectetur elited</div></div>
  </div>

  <div class="abs" style="left:684px;top:3724px">
    <div class="f-head">Company</div>
    <ul class="f-links"><li>Home</li><li>About Us</li><li>Services</li><li>Blog</li><li>Contact us</li></ul>
  </div>

  <div class="abs" style="left:850px;top:3724px;width:240px">
    <div class="f-head">Stil have questios?</div>
    <p style="font-size:12.5px;line-height:19px;margin-top:14px">Contact us using this form. A representative will aswer your questions as soon as possible.</p>
  </div>
  <a class="btn" style="left:850px;top:3855px;width:193px;height:42px;font-size:15px">GET IN TOUCH</a>

  <div class="abs divider"></div>
  <div class="abs goup"><svg width="10" height="10" viewBox="0 0 10 10"><path d="M5 9V2M2 5l3-3 3 3" stroke="#fff" stroke-width="1.6" fill="none"/></svg>Go Up</div>
  <div class="abs bottom" style="left:113px">© 2023 VIEWNOVA | All Rights Reserved</div>
  <div class="abs bottom" style="left:765px">Privacy Policy &nbsp;|&nbsp; Cookie Policy &nbsp;|&nbsp; Terms Of Services</div>
</footer>

</div>
</body>
</html>
```